Word document template for sales proposals

I am after a template that is simple but impactful. Use of colour to be limited but some for impact would be good. The proposals are for use in the professional technical field.

```html
<!DOCTYPE html>
<html lang="en">
<head>
<meta charset="utf-8">
<title>Sales Proposal Template</title>
<link href="https://fonts.googleapis.com/css2?family=Lato:wght@300;400&display=swap" rel="stylesheet">
<style>
  :root {
    --brand-blue: #29a9e1;
    --brand-orange: #f7941d;
    --ink: #111111;
    --rule: #e4e4e4;
    --paper: #ffffff;
  }
  html, body {
    margin: 0;
    padding: 0;
    overflow: hidden;
    background: var(--paper);
  }
  .page {
    position: relative;
    width: 849px;
    height: 1200px;
    overflow: hidden;
    background: var(--paper);
    font-family: "Lato", sans-serif;
    color: var(--ink);
  }
  .header-band {
    position: absolute;
    left: 0;
    top: 110px;
    width: 616px;
    height: 23px;
    background: var(--brand-blue);
  }
  .brand {
    position: absolute;
    left: 622px;
    top: 88px;
    display: flex;
    align-items: center;
    gap: 10px;
  }
  .brand-dot {
    width: 56px;
    height: 56px;
    border-radius: 50%;
    background: var(--brand-blue);
  }
  .brand-name {
    font-family: "Lato", sans-serif;
    font-weight: 400;
    font-size: 42px;
    letter-spacing: 4px;
    color: var(--brand-orange);
    line-height: 1;
  }
  .block {
    position: absolute;
    left: 101px;
    margin: 0;
  }
  .section-title {
    font-weight: 300;
    font-size: 34px;
    line-height: 40px;
  }
  .sub-title {
    font-weight: 400;
    font-size: 18.5px;
    line-height: 24px;
  }
  .body-text {
    font-weight: 400;
    font-size: 14.4px;
    line-height: 22px;
    letter-spacing: 0.15px;
    width: 650px;
  }
  .needs-lead { left: 151px; }
  .needs-list {
    left: 172px;
    list-style: none;
    padding: 0;
  }
  .needs-list li {
    position: relative;
    padding-left: 29px;
  }
  .needs-list li::before {
    content: "";
    position: absolute;
    left: 5px;
    top: 8px;
    width: 6px;
    height: 6px;
    border: 1px solid var(--ink);
    border-radius: 50%;
  }
  .criteria-table {
    position: absolute;
    left: 101px;
    top: 772px;
    width: 648px;
    border-collapse: collapse;
    font-size: 14.4px;
    letter-spacing: 0.15px;
  }
  .criteria-table th,
  .criteria-table td {
    text-align: left;
    font-weight: 400;
    padding: 0 7px;
    border: 1px solid var(--rule);
  }
  .criteria-table th {
    height: 31px;
    background: var(--brand-blue);
    border-color: var(--brand-blue);
  }
  .criteria-table td { height: 33px; }
  .criteria-table .col-criteria { width: 441px; }
</style>
</head>
<body>
<div class="page">
  <div class="header-band"></div>
  <div class="brand">
    <span class="brand-dot"></span>
    <span class="brand-name">K7RN</span>
  </div>

  <h1 class="block section-title" style="top:182px;">Executive Summary</h1>
  <p class="block body-text" style="top:240px;">Briefly outline the challenges your firm can help the prospective organization solve.&nbsp; Provide a concise summary of your solution’s key deliverables, project timelines, pricing, and any other relevant information to influence decision-makers who may only read this part.</p>

  <h1 class="block section-title" style="top:322px;">Our Understanding</h1>

  <h2 class="block sub-title" style="top:382px;">Your Company</h2>
  <p class="block body-text" style="top:419px;">Paraphrase prospect’s corporate overview from their website.</p>

  <h2 class="block sub-title" style="top:460px;">Your Needs</h2>
  <p class="block body-text" style="top:485px;">Provide a brief description of the prospect’s needs.&nbsp; Consider using a bulleted list that is prioritized from critical needs to value adds.</p>
  <p class="block body-text needs-lead" style="top:550px;">Prioritized list of needs:</p>
  <ul class="block body-text needs-list" style="top:584px;">
    <li>Need 1</li>
    <li>Need 2</li>
    <li>Need 3</li>
  </ul>

  <h2 class="block sub-title" style="top:669px;">Decision Criteria</h2>
  <p class="block body-text" style="top:694px;">Decision, including service level agreements, warranties, professional services, &nbsp;&nbsp;&nbsp;delivery timelines, etc.</p>

  <table class="criteria-table">
    <thead>
      <tr><th class="col-criteria">Key Decision Criteria</th><th>Importance</th></tr>
    </thead>
    <tbody>
      <tr><td>1.&nbsp; Service Level Agreement</td><td>High</td></tr>
      <tr><td>2.&nbsp; Pricing</td><td>Med</td></tr>
      <tr><td>3.&nbsp; Available before June 1st</td><td>High</td></tr>
      <tr><td>4. Something Else here</td><td>Med</td></tr>
      <tr><td>5. Write more if you need or delete this line</td><td>High</td></tr>
      <tr><td>6. This is another extra line</td><td>Low</td></tr>
    </tbody>
  </table>
</div>
</body>
</html>
```